Business Card Design for Training Business

Clear Path Coaching is a new business that delivers training and other services with a focus on topics related to mental health and wellbeing, for example, Wellmind Response Course, Resilience etc. We have a strong focus on evidence-based psychology and neuroscience. I have a logo which I will upload with the brief, so please consider colours that work well with the logo.
Target Market(s)
Adults, workplaces (particularly government and not-for-profits)
Industry/Entity Type
Business
Contact Information for Business Card
Head Strong TrainingSamantha SellwoodDirector0438 770 850sam@headstrongtraining.com.auwww.headstrongtraining.com.au

```html
<!DOCTYPE html>
<html lang="en">
<head>
<meta charset="utf-8">
<title>Clear Path Coaching – Business Card</title>
<link href="https://fonts.googleapis.com/css2?family=Arimo:wght@400&family=Montserrat:wght@300&display=swap" rel="stylesheet">
<style>
  :root {
    --backdrop: #3a3430;
    --card: #1b1b1c;
    --teal: #2db7b5;
    --mark-grey: #8e8e8e;
    --text-white: #f2f2f2;
    --rule: #6a6a6a;
  }
  * { margin: 0; padding: 0; box-sizing: border-box; }
  html, body {
    width: 1200px; height: 787px; overflow: hidden;
    background: var(--backdrop);
  }
  .stage {
    position: relative; width: 1200px; height: 787px;
  }
  .card {
    position: absolute; top: 234px;
    width: 530px; height: 320px;
    background: var(--card);
    box-shadow: 0 10px 28px rgba(0,0,0,.45);
    overflow: hidden;
  }
  .card--back { left: 40px; }
  .card--front { left: 630px; }

  .brand {
    position: absolute; left: 0; right: 0;
    display: flex; flex-direction: column; align-items: center;
  }
  .brand__dot {
    width: 74px; height: 74px; border-radius: 50%;
    border: 2px solid currentColor;
    margin-bottom: 14px;
  }
  .brand__name {
    font-family: "Montserrat", sans-serif; font-weight: 300;
    font-size: 21px; letter-spacing: 4px; text-transform: uppercase;
    color: var(--mark-grey);
  }
  .card--back .brand { top: 66px; }
  .card--back .brand__dot { color: var(--mark-grey); }
  .card--back .website {
    position: absolute; left: 0; right: 0; bottom: 62px; text-align: center;
    font-family: "Arimo", sans-serif; font-size: 15px; color: var(--text-white);
  }

  .card--front .brand { top: 40px; }
  .card--front .brand__dot { color: var(--teal); }

  .person {
    position: absolute; right: 314px; top: 196px; text-align right;
    text-align: right;
    font-family: "Arimo", sans-serif;
    white-space: nowrap;
  }
  .person__name { font-size: 22px; color: var(--teal); }
  .person__role { font-size: 15px; color: var(--text-white); margin-top: 6px; }

  .divider {
    position: absolute; left: 232px; top: 190px;
    width: 1px; height: 88px; background: var(--rule);
  }

  .contacts {
    position: absolute; left: 248px; top: 196px;
    list-style: none;
    font-family: "Arimo", sans-serif; font-size: 13.5px; color: var(--text-white);
    white-space: nowrap;
  }
  .contacts li { display: flex; align-items: center; height: 27px; }
  .contacts svg { width: 16px; height: 16px; margin-right: 11px; flex: none; fill: var(--teal); }
</style>
</head>
<body>
<main class="stage">

  <section class="card card--back" aria-label="Card back">
    <div class="brand">
      <span class="brand__dot"></span>
      <span class="brand__name">Clear Path Coaching</span>
    </div>
    <p class="website">www.clearpathcoaching.example.au</p>
  </section>

  <section class="card card--front" aria-label="Card front">
    <div class="brand">
      <span class="brand__dot"></span>
      <span class="brand__name">Clear Path Coaching</span>
    </div>

    <div class="person">
      <p class="person__name">Rebecca Tanfield</p>
      <p class="person__role">Director</p>
    </div>

    <span class="divider"></span>

    <ul class="contacts">
      <li>
        <svg viewBox="0 0 16 16" aria-hidden="true"><path d="M3 1h3l1 4-2 1.5c.8 1.8 2.2 3.2 4 4L10.5 8.5l4 1v3c0 1-1 2-2 2C6.5 14.5 1.5 9.5 1.5 3c0-1 .5-2 1.5-2z"/></svg>
        0491 362 517
      </li>
      <li>
        <svg viewBox="0 0 16 16" aria-hidden="true"><path d="M1 3h14v10H1z M1.5 3.5 8 9l6.5-5.5" fill="none" stroke="var(--teal)" stroke-width="1.6"/></svg>
        bec@clearpathcoaching.example.au
      </li>
      <li>
        <svg viewBox="0 0 16 16" aria-hidden="true"><circle cx="8" cy="8" r="7"/><path d="M1 8h14M8 1c-3 3-3 11 0 14M8 1c3 3 3 11 0 14" fill="none" stroke="var(--card)" stroke-width="1.2"/></svg>
        www.clearpathcoaching.example.au
      </li>
    </ul>
  </section>

</main>
</body>
</html>
```